8x8 Social Media Ad - Brant Summit Expo

Attention Real Estate Agents
Please join us for our
Quarterly Real Estate Training Expo
The 2nd Saturday of February, May, August and November
Our Next Training Expo is _________________________________
From 9 am to 1 pm
at
Halvorne Suites Millbrook Court
4817 Copper Willow Lane, Dunmere, MD 20588
Scheduled Speakers
9:00 am - Marcus Pellington - Orientation
9:30 am - Derrin Oakfield - Multiple Income Streams / Crest Program
10:00 am - Talia Brennick - Marketing though Social Media
10:45 am - Rex Dunmore - Generating Business through Ru-Plaza
11:30 am - Kemi Adeyoro - Real Estate Investing
12:15 pm - Gregor Tamsey - (Main Speaker) Training Topic TBA
For more information call Marcus Pellington at (240) 555-0183 or email mpellington@brantsummithomes.example

```html
<!DOCTYPE html>
<html lang="en">
<head>
<meta charset="utf-8">
<title>Brant Summit Expo – Quarterly Real Estate Training Expo</title>
<link rel="stylesheet" href="https://fonts.googleapis.com/css2?family=Montserrat:wght@400;500;600;700;800&family=Roboto:wght@700&family=Kaushan+Script&display=swap">
<style>
  :root {
    --teal-deep: #236f6d;
    --teal: #2b7d7a;
    --teal-bright: #1b8d8a;
    --teal-text: #178582;
    --ink: #2b2b2b;
    --white: #ffffff;
    --paper: #f4f6f6;
    --frame-fill-top: #d9dadb;
    --frame-fill-bottom: #9a9ea0;
  }
  * { box-sizing: border-box; margin: 0; padding: 0; }
  html, body { width: 1200px; height: 1200px; overflow: hidden; }
  body {
    position: relative;
    background: var(--paper);
    font-family: "Montserrat", sans-serif;
    color: var(--ink);
  }
  .hero {
    position: absolute; left: 0; top: 0; width: 1200px; height: 690px;
    background: linear-gradient(180deg, var(--teal) 0%, var(--teal-deep) 55%, #2f8380 100%);
  }
  .hero-scene {
    position: absolute; left: 90px; top: 160px; width: 1020px; height: 520px;
    background: radial-gradient(ellipse at 50% 40%, rgba(255,255,255,0.08), rgba(0,0,0,0.06) 70%, transparent 100%);
  }
  .lower {
    position: absolute; left: 0; top: 690px; width: 1200px; height: 510px;
    background: linear-gradient(180deg, #ffffff 0%, #f1f3f3 100%);
  }
  .center { position: absolute; left: 0; width: 1200px; text-align: center; }
  .invite { top: 42px; font-size: 21px; font-weight: 500; color: var(--white); }
  .title {
    top: 76px; font-family: "Roboto", sans-serif; font-weight: 700;
    font-size: 72px; letter-spacing: -0.5px; color: var(--white);
  }
  .script {
    top: 152px; font-family: "Kaushan Script", cursive; font-size: 92px;
    color: var(--white); line-height: 1.2;
  }
  .dates {
    position: absolute; left: 190px; top: 285px; width: 820px; height: 46px;
    background: linear-gradient(90deg, #e9eced, #ffffff);
    border-radius: 10px 14px 14px 10px;
    display: flex; align-items: center; justify-content: center; gap: 14px;
    font-size: 23px; color: var(--teal-text);
  }
  .dates strong { font-weight: 700; color: var(--teal-deep); }
  .hours {
    top: 350px; font-size: 50px; font-weight: 800; color: var(--white);
    text-shadow: 2px 3px 0 rgba(0,0,0,0.35);
  }
  .speaker-photo {
    position: absolute; top: 433px; width: 205px; height: 305px;
    border-radius: 52px 52px 0 0;
    border: 6px solid var(--teal-bright); border-bottom: none; border-left-width: 0;
    background: linear-gradient(180deg, var(--frame-fill-top), var(--frame-fill-bottom));
    overflow: hidden;
  }
  .schedule-label {
    position: absolute; left: 112px; top: 830px; width: 160px; text-align: center;
    font-size: 21px; font-weight: 500; line-height: 29px;
  }
  .schedule-label svg { display: block; margin: 0 auto 4px; }
  .divider { position: absolute; width: 1px; background: #9aa3a3; }
  .schedule { position: absolute; top: 770px; left: 0; }
  .row { position: absolute; height: 35px; font-size: 19px; font-weight: 500; white-space: nowrap; line-height: 35px; }
  .time { left: 333px; color: var(--teal-text); }
  .name { left: 469px; }
  .topic { left: 670px; }
  .address-band {
    position: absolute; left: 0; top: 1002px; width: 1200px; height: 43px;
    background: linear-gradient(90deg, var(--teal-deep), var(--teal-bright));
    display: flex; align-items: center; justify-content: center; gap: 12px;
    color: var(--white); font-size: 20px; font-weight: 600;
  }
  .brand {
    position: absolute; left: 34px; top: 1066px; width: 210px; height: 110px;
    background: var(--white);
    display: flex; flex-direction: column; align-items: center; justify-content: center;
    color: var(--teal-deep); font-weight: 700; font-size: 22px; line-height: 1.15; text-align: center;
  }
  .info-call {
    position: absolute; left: 333px; top: 1071px; height: 39px;
    display: flex; align-items: center; gap: 12px; font-size: 21px; font-weight: 500;
  }
  .info-pill {
    background: var(--teal-bright); color: var(--white); font-weight: 700; font-size: 20px;
    height: 39px; line-height: 39px; padding: 0 18px; border-radius: 10px 14px 14px 10px;
  }
  .contact-row {
    position: absolute; left: 340px; top: 1128px; display: flex; gap: 34px;
    font-size: 18px; font-weight: 500;
  }
  .contact-row span { display: flex; align-items: center; gap: 10px; }
</style>
</head>
<body>
  <section class="hero">
    <div class="hero-scene" role="img" aria-label="Faint photo of a two-storey house behind the headline"></div>
    <p class="center invite">Please join us for our</p>
    <h1 class="center title">QUARTERLY REAL ESTATE</h1>
    <p class="center script">Training Expo</p>
    <div class="dates"><span>The 2nd Saturday of</span><strong>February, May, August and November</strong></div>
    <p class="center hours">From 9 am to 1 pm</p>
  </section>

  <section class="lower"></section>

  <div class="speaker-photo" style="left:54px" role="img" aria-label="Photo of speakers Marcus Pellington and Talia Brennick"></div>
  <div class="speaker-photo" style="left:278px" role="img" aria-label="Photo of speaker Derrin Oakfield"></div>
  <div class="speaker-photo" style="left:502px" role="img" aria-label="Photo of speaker Rex Dunmore"></div>
  <div class="speaker-photo" style="left:724px" role="img" aria-label="Photo of speaker Kemi Adeyoro"></div>
  <div class="speaker-photo" style="left:948px" role="img" aria-label="Photo of main speaker Gregor Tamsey"></div>

  <div class="schedule-label">
    <svg width="22" height="28" viewBox="0 0 22 28" aria-hidden="true">
      <circle cx="11" cy="7" r="6" fill="#178582"/>
      <path d="M0 28v-5a7 7 0 0 1 7-7h8a7 7 0 0 1 7 7v5z" fill="#178582"/>
    </svg>
    Scheduled<br>Speakers
  </div>

  <div class="divider" style="left:303px; top:782px; height:188px"></div>
  <div class="divider" style="left:446px; top:782px; height:188px"></div>
  <div class="divider" style="left:648px; top:782px; height:188px"></div>

  <div class="schedule">
    <div class="row time" style="top:0">9:00 am</div>
    <div class="row name" style="top:0">Marcus Pellington</div>
    <div class="row topic" style="top:0">Orientation</div>
    <div class="row time" style="top:35px">9:30 am</div>
    <div class="row name" style="top:35px">Derrin Oakfield</div>
    <div class="row topic" style="top:35px">Multiple Income Streams / Crest Program</div>
    <div class="row time" style="top:70px">10:00 am</div>
    <div class="row name" style="top:70px">Talia Brennick</div>
    <div class="row topic" style="top:70px">Marketing though Social Media</div>
    <div class="row time" style="top:105px">10:45 am</div>
    <div class="row name" style="top:105px">Rex Dunmore</div>
    <div class="row topic" style="top:105px">Generating Business through Ru-Plaza</div>
    <div class="row time" style="top:140px">11:30 am</div>
    <div class="row name" style="top:140px">Kemi Adeyoro</div>
    <div class="row topic" style="top:140px">Real Estate Investing</div>
    <div class="row time" style="top:175px">12:15 pm</div>
    <div class="row name" style="top:175px">Gregor Tamsey</div>
    <div class="row topic" style="top:175px">(Main Speaker) Training Topic TBA</div>
  </div>

  <div class="address-band">
    <svg width="18" height="24" viewBox="0 0 18 24" aria-hidden="true">
      <path d="M9 0a9 9 0 0 0-9 9c0 6.5 9 15 9 15s9-8.5 9-15a9 9 0 0 0-9-9zm0 13a4 4 0 1 1 0-8 4 4 0 0 1 0 8z" fill="#ffffff"/>
    </svg>
    <span>Halvorne Suites Millbrook Court 4817 Copper Willow Lane, Dunmere, MD 20588</span>
  </div>

  <div class="brand">Brant Summit<br>Realty Group</div>
  <div class="divider" style="left:303px; top:1090px; height:65px"></div>

  <div class="info-call">
    <span>For more information call</span>
    <span class="info-pill">Marcus Pellington at (240) 555-0183</span>
  </div>

  <div class="contact-row">
    <span>
      <svg width="16" height="12" viewBox="0 0 16 12" aria-hidden="true"><rect width="16" height="12" rx="1" fill="#178582"/><path d="M1 1l7 6 7-6" stroke="#fff" stroke-width="1.4" fill="none"/></svg>
      email mpellington@brantsummithomes.example
    </span>
    <span>
      <svg width="16" height="16" viewBox="0 0 16 16" aria-hidden="true"><circle cx="8" cy="8" r="7" fill="none" stroke="#178582" stroke-width="1.6"/><path d="M1 8h14M8 1c3 3 3 11 0 14M8 1c-3 3-3 11 0 14" stroke="#178582" stroke-width="1.2" fill="none"/></svg>
      www.brantsummithomes.example
    </span>
  </div>
</body>
</html>
```